KRT Engineering Business Card Design

We’re looking for an elegant, clean, and timeless business card design that communicates experience, capability, and reliability.

KRT Engineering was established in 1995 , we are a Government Contracting company providing Professional Services to the Office of Frontier Affairs, Harbor Protection and the Vantage Collective. Our capabilities include: Acquisition & Program Management; Intelligence & Security Operations; Cyber, IT & Network Operations; Lifecycle Logistics & Asset Readiness; C5ISR Systems Engineering & Sustainment.

We want the card to reflect a straightforward, confident approach to business. The design should feel polished and professional without being flashy or overly corporate.

Design Direction
Clean, sophisticated, and uncluttered
Elegant but understated
Strong typography and thoughtful spacing
A timeless aesthetic rather than something overly trendy
Confident and established, with a sense of substance
Easy to read and practical in a real-world business setting

The overall impression should be: “These are experienced professionals who know what they’re doing, do what they say, and can be relied upon.”

We’re open to creative interpretations. The finished card should feel distinctive through its typography, proportions, layout, and attention to detail rather than through excessive graphics or visual effects.

We’re looking for a design that would make a potential client immediately feel that they’re dealing with a capable, trustworthy, and established company.

Company Colors: Navy and Gold/Yellow (but you do not need to use these colors on the card)
Company Name: KRT Engineering Associates, Inc. (known as KRT Engineering)
Website: krtengineering.com
Company Logo: Navy & Gold (other variations attached)

```html
<!DOCTYPE html>
<html lang="en">
<head>
<meta charset="utf-8">
<title>KRT Engineering – Business Card</title>
<link href="https://fonts.googleapis.com/css2?family=Poppins:wght@400;500;700;800&display=swap" rel="stylesheet">
<style>
  :root {
    --stage: #2b2e34;
    --navy: #222b5e;
    --gold: #f6dc3f;
    --white: #ffffff;
    --soft-white: #e4e7f2;
    --rule: rgba(255, 255, 255, 0.35);
  }
  * { box-sizing: border-box; margin: 0; padding: 0; }
  html, body {
    width: 1200px;
    height: 985px;
    overflow: hidden;
    background: var(--stage);
    font-family: "Poppins", sans-serif;
  }
  .sheet {
    width: 1200px;
    height: 985px;
    display: flex;
    flex-direction: column;
    align-items: center;
    justify-content: center;
    gap: 60px;
  }
  .card {
    position: relative;
    width: 700px;
    height: 400px;
    background: var(--navy);
    border-radius: 26px;
    overflow: hidden;
  }

  /* Wordmark */
  .wordmark {
    display: flex;
    align-items: center;
    gap: 18px;
  }
  .wordmark__name {
    font-weight: 800;
    color: var(--white);
    letter-spacing: -2px;
    line-height: 1;
  }
  .wordmark__dot {
    border-radius: 50%;
    background: var(--gold);
    flex: none;
  }

  /* Back side */
  .card--back {
    display: flex;
    flex-direction: column;
    align-items: center;
    justify-content: center;
    gap: 34px;
  }
  .card--back .wordmark__name { font-size: 150px; }
  .card--back .wordmark__dot { width: 34px; height: 34px; }
  .card__website {
    font-size: 17px;
    font-weight: 400;
    color: var(--white);
    letter-spacing: 4px;
  }

  /* Front side */
  .card--front .wordmark {
    position: absolute;
    left: 60px;
    top: 110px;
  }
  .card--front .wordmark__name { font-size: 104px; }
  .card--front .wordmark__dot { width: 24px; height: 24px; }
  .divider {
    position: absolute;
    left: 375px;
    top: 70px;
    width: 1px;
    height: 200px;
    background: var(--rule);
  }
  .contact-block {
    position: absolute;
    left: 410px;
    top: 80px;
  }
  .person__name {
    font-size: 25px;
    font-weight: 700;
    color: var(--gold);
    letter-spacing: 0.5px;
    line-height: 1.1;
  }
  .person__title {
    font-size: 17px;
    font-weight: 400;
    color: var(--white);
    margin-bottom: 22px;
  }
  .contact-list { list-style: none; }
  .contact-list__item {
    display: flex;
    align-items: center;
    gap: 10px;
    font-size: 16px;
    color: var(--white);
    margin-bottom: 9px;
  }
  .contact-list__icon {
    width: 20px;
    height: 20px;
    flex: none;
  }
  .address {
    position: absolute;
    left: 60px;
    right: 60px;
    bottom: 44px;
    font-size: 16px;
    color: var(--soft-white);
    letter-spacing: 0.3px;
  }
</style>
</head>
<body>
<main class="sheet">

  <section class="card card--back" aria-label="Card back">
    <div class="wordmark">
      <span class="wordmark__name">KRT</span>
      <span class="wordmark__dot"></span>
    </div>
    <p class="card__website">www.krtengineering.com</p>
  </section>

  <section class="card card--front" aria-label="Card front">
    <div class="wordmark">
      <span class="wordmark__name">KRT</span>
      <span class="wordmark__dot"></span>
    </div>

    <div class="divider"></div>

    <div class="contact-block">
      <h1 class="person__name">MARCUS HALE</h1>
      <p class="person__title">Manager</p>
      <ul class="contact-list">
        <li class="contact-list__item">
          <svg class="contact-list__icon" viewBox="0 0 20 20" aria-hidden="true">
            <circle cx="10" cy="10" r="10" fill="#f6dc3f"/>
            <path d="M6.6 5.2l1.6-.3 1 2.4-1.1.9a6 6 0 0 0 3 3l.9-1.1 2.4 1-.3 1.6c-.1.5-.6.8-1.1.8A8.3 8.3 0 0 1 5.8 6.3c0-.5.3-1 .8-1.1z" fill="#222b5e"/>
          </svg>
          555-318-2047
        </li>
        <li class="contact-list__item">
          <svg class="contact-list__icon" viewBox="0 0 20 20" aria-hidden="true">
            <circle cx="10" cy="10" r="10" fill="#f6dc3f"/>
            <rect x="5" y="6.5" width="10" height="7" rx="1" fill="#222b5e"/>
            <path d="M5.5 7l4.5 3.5L14.5 7" fill="none" stroke="#f6dc3f" stroke-width="1"/>
          </svg>
          marcus.hale@krtmail.com
        </li>
        <li class="contact-list__item">
          <svg class="contact-list__icon" viewBox="0 0 20 20" aria-hidden="true">
            <circle cx="10" cy="10" r="10" fill="#f6dc3f"/>
            <g fill="none" stroke="#222b5e" stroke-width="1.1">
              <circle cx="10" cy="10" r="5"/>
              <ellipse cx="10" cy="10" rx="2.2" ry="5"/>
              <path d="M5 10h10M5.8 7.5h8.4M5.8 12.5h8.4"/>
            </g>
          </svg>
          www.krtengineering.com
        </li>
      </ul>
    </div>

    <p class="address">1420 Harbor View Lane, Suite 310, Bayport, VA 23000</p>
  </section>

</main>
</body>
</html>
```